Bespoke Builders Business Card Design

We need a business card for an established builder of high quality bespoke homes in Auckland and Northland. We build and renovate homes collaboratively facilitating effective communication between owners, builders, architects, suppliers and tradespeople. We have never built or renovated a home that leaks or has faults. We only use reliable materials. We have never been sued or had legal action taken against us. We are honest builders of bespoke homes not group mass produced homes. Our niche market is in character homes. We practice sustainability and have built a lot of coastal property. We have been in business for over thirty years . We would like to see natural colors of the environment sand,sea and maybe vegetation . The design should communicate quality, sustainability,fair pricing, open communication and the originality of bespoke building. And the fact that the builder is registered.

Industry/Entity Type

Business

Contact Information for Business Card

Rowan Tellick Builders
Ph. 021583917
18 Kestrel Rd Harwood Bay Auckland 0814
PO Box 927 Mangawhai 0583

```html
<!DOCTYPE html>
<html lang="en">
<head>
<meta charset="utf-8">
<title>Rowan Tellick Builders – Business Card</title>
<link rel="stylesheet" href="https://fonts.googleapis.com/css2?family=Libre+Bodoni:wght@500;700&family=Source+Sans+3:wght@400&display=swap">
<style>
  :root {
    --backdrop: #e7e4df;
    --card-white: #ffffff;
    --card-black: #000000;
    --brand-blue: #2b2f8c;
    --rule-black: #111111;
    --text-light: #ffffff;
  }
  html, body {
    margin: 0;
    padding: 0;
    width: 1189px;
    height: 1200px;
    overflow: hidden;
    background: var(--backdrop);
  }
  .canvas {
    position: relative;
    width: 1189px;
    height: 1200px;
  }
  .card {
    position: absolute;
    left: 140px;
    width: 917px;
    height: 524px;
    box-shadow: 0 4px 10px rgba(0,0,0,0.25);
    overflow: hidden;
  }

  /* Front card */
  .card--front { top: 45px; background: var(--card-black); }
  .front__header {
    position: absolute;
    left: 0; top: 0;
    width: 100%;
    height: 261px;
    background: var(--card-white);
  }
  .front__title-row {
    position: absolute;
    left: 0; right: 0;
    top: 110px;
    display: flex;
    align-items: center;
    transform: translateY(-50%);
  }
  .front__rule {
    flex: 1;
    height: 3px;
    background: var(--rule-black);
  }
  .front__name {
    margin: 0 10px;
    font-family: "Libre Bodoni", "Bodoni Moda", serif;
    font-weight: 700;
    font-size: 56px;
    line-height: 1;
    color: var(--brand-blue);
    white-space: nowrap;
    letter-spacing: 0.5px;
  }
  .front__band {
    position: absolute;
    left: 0; top: 261px;
    width: 100%;
    height: 27px;
    background: var(--brand-blue);
  }
  .front__contact {
    position: absolute;
    left: 0; right: 0;
    top: 345px;
    margin: 0;
    text-align: center;
    font-family: "Source Sans 3", "Myriad Pro", sans-serif;
    font-size: 28px;
    line-height: 45px;
    color: var(--text-light);
    font-style: normal;
    letter-spacing: 0.4px;
  }

  /* Back card */
  .card--back {
    top: 624px;
    background: var(--card-black);
    border: 13px solid var(--brand-blue);
    box-sizing: border-box;
  }
  .back__name {
    position: absolute;
    left: 0; right: 0;
    top: 244px;
    transform: translateY(-50%);
    margin: 0;
    text-align: center;
    font-family: "Libre Bodoni", "Bodoni Moda", serif;
    font-weight: 700;
    font-size: 64px;
    line-height: 1;
    color: var(--text-light);
    white-space: nowrap;
    letter-spacing: 0.5px;
  }
</style>
</head>
<body>
  <main class="canvas">
    <section class="card card--front" aria-label="Business card front">
      <div class="front__header">
        <div class="front__title-row">
          <span class="front__rule"></span>
          <h1 class="front__name">Rowan Tellick Builders</h1>
          <span class="front__rule"></span>
        </div>
      </div>
      <div class="front__band"></div>
      <address class="front__contact">
        021583917<br>
        18 Kestrel Rd Harwood Bay Auckland 0814<br>
        PO Box 927 Mangawhai 0583
      </address>
    </section>

    <section class="card card--back" aria-label="Business card back">
      <h2 class="back__name">Rowan Tellick Builders</h2>
    </section>
  </main>
</body>
</html>
```